Tandem Hearth Works Pty Ltd

We need business cards for a company based in Perth, we install, service and maintain fire equipment.
On the front we want a great design with our logo and a small spot for our full company name, general company email address and office number. On the back we need space for our name, title, mobile number and email address on the back.

Target Market(s)

Facility managers and commercial/industrial building owners/occupiers.

Contact Information for Business Card

Font styles to use
Sans Serif

Requirements
Must have
• Please only submit 5 of your best samples.
Darker tones are preferred.
Nice to have
• We want to use, black, red and grey. Keep it modern and clean.
I've attached the company logo and a sample of a boarder we use on our emergency plans.
Should not have
• No preference. Let the designer choose.

```html
<!DOCTYPE html>
<html lang="en">
<head>
<meta charset="utf-8">
<title>Tandem Hearth Works – Business Cards</title>
<link href="https://fonts.googleapis.com/css2?family=Montserrat:wght@400;500;600;700&family=Roboto:wght@300;400&display=swap" rel="stylesheet">
<style>
  :root {
    --backdrop: #4a4a4d;
    --card: #0b0b0c;
    --card-edge: #151516;
    --red: #ee1c25;
    --white: #f2f2f2;
    --grey: #5a5a5c;
    --emboss: #1c1c1e;
  }
  * { margin: 0; padding: 0; box-sizing: border-box; }
  html, body { width: 1200px; height: 1200px; overflow: hidden; }
  body {
    background: var(--backdrop);
    font-family: "Roboto", sans-serif;
    position: relative;
  }
  .card {
    position: absolute;
    left: 160px;
    width: 880px;
    height: 503px;
    background: linear-gradient(160deg, var(--card-edge), var(--card) 60%);
    border-radius: 28px;
    overflow: hidden;
  }
  .card--front { top: 70px; }
  .card--back { top: 627px; }

  /* Front */
  .front-mark {
    position: absolute;
    top: 170px;
    left: 0;
    width: 100%;
    text-align: center;
    font-family: "Montserrat", sans-serif;
    font-weight: 700;
    font-size: 64px;
    letter-spacing: 2px;
    color: var(--emboss);
  }
  .front-details {
    position: absolute;
    top: 372px;
    left: 0;
    width: 100%;
    text-align: center;
    color: var(--grey);
    font-size: 19px;
    line-height: 1.45;
  }
  .front-details .dot {
    display: inline-block;
    width: 6px; height: 6px;
    background: var(--red);
    border-radius: 50%;
    vertical-align: middle;
    margin: 0 8px;
  }

  /* Back */
  .person {
    position: absolute;
    top: 56px;
    left: 62px;
    font-family: "Montserrat", sans-serif;
  }
  .person__name {
    color: var(--red);
    font-weight: 600;
    font-size: 25px;
    letter-spacing: 5px;
  }
  .person__title {
    color: var(--white);
    font-weight: 400;
    font-size: 15px;
    letter-spacing: 5px;
    margin-top: 4px;
  }
  .person__rule {
    width: 40px;
    height: 2px;
    background: var(--red);
    margin-top: 10px;
  }
  .contact {
    position: absolute;
    left: 62px;
    bottom: 62px;
    display: grid;
    grid-template-columns: 90px auto;
    row-gap: 8px;
    font-size: 18px;
    letter-spacing: 2px;
  }
  .contact dt { color: var(--red); font-weight: 300; }
  .contact dd { color: var(--white); font-weight: 400; }
  .back-mark {
    position: absolute;
    right: 70px;
    bottom: 66px;
    font-family: "Montserrat", sans-serif;
    font-weight: 700;
    font-size: 40px;
    line-height: 1.05;
    text-align: right;
    color: var(--red);
  }
</style>
</head>
<body>
  <section class="card card--front">
    <div class="front-mark">TANDEM HEARTH</div>
    <div class="front-details">
      <div><span class="dot"></span>Tandem Hearth Works Pty Ltd<span class="dot"></span></div>
      <div>123 456 7890 | youremail.com</div>
    </div>
  </section>

  <section class="card card--back">
    <div class="person">
      <div class="person__name">MARCUS REYNE</div>
      <div class="person__title">FOUNDER &amp; CEO</div>
      <div class="person__rule"></div>
    </div>
    <dl class="contact">
      <dt>tel:</dt><dd>+61 400 218 574</dd>
      <dt>email:</dt><dd>ceo@tandemhearth.com</dd>
      <dt>web:</dt><dd>www.tandemhearth.com</dd>
    </dl>
    <div class="back-mark">TANDEM<br>HEARTH</div>
  </section>
</body>
</html>
```